Executive Taxi firm with Chauffeur service Website

I have my domain name registered and I have started to work on my site but I am struggling. I am just about to get a logo for the company and need a web site that clearly represents the fact we are an executive/luxury brand in private hire vehicles. We offer airport transfers, train station transfers, seaport transfers, holiday transfers and business to business pick up and drop off.

Target Market(s)

Corporate people, holidaymakers looking for a luxury start their holiday. VIPs' and celebrities.

Number of Pages Required

5+ page

Font styles to use
Serif
Sans Serif
Decorative
Script

Colors

Designer to choose colors to be used in the design.

Requirements
Must have
• Home Page, Services, About Us, VIP and Contact us
• Please see www.brivomotors.co.uk I have started it but not happy with it at all.
Nice to have
• Booking form or enquiry form.

```html
<!DOCTYPE html>
<html lang="en">
<head>
<meta charset="utf-8">
<title>Marlow Travel — Executive Taxi &amp; Chauffeur Service</title>
<link rel="stylesheet" href="https://fonts.googleapis.com/css2?family=Montserrat:wght@400;500;600;700&family=Open+Sans:ital,wght@0,400;0,600;1,400&display=swap">
<style>
:root{
  --yellow:#f2c414;
  --blue:#1f5aa6;
  --blue-deep:#173f7a;
  --ink:#1b1b1b;
  --muted:#6b6b6b;
  --pale:#f0f5fa;
  --footer:#121212;
  --white:#ffffff;
  --line:#c9c9c9;
}
*{box-sizing:border-box;margin:0;padding:0}
html,body{width:1200px;height:3600px;overflow:hidden}
body{position:relative;background:var(--white);font-family:"Open Sans",Arial,sans-serif;color:var(--ink)}
.abs{position:absolute}

/* hero */
.hero{position:absolute;left:0;top:0;width:1200px;height:612px;overflow:hidden}
.hero-photo{position:absolute;inset:0;background:
  radial-gradient(ellipse 420px 260px at 900px 330px,#d9a825 0%,rgba(217,168,37,.55) 35%,rgba(0,0,0,0) 70%),
  linear-gradient(100deg,#2a3a55 0%,#46577a 40%,#6b7690 70%,#3b4458 100%)}
.hero-shade{position:absolute;inset:0;background:linear-gradient(90deg,rgba(10,20,40,.55),rgba(10,20,40,0) 60%)}
.brand{position:absolute;left:111px;top:32px;display:flex;align-items:center;gap:18px}
.brand-mark{width:90px;height:90px;border-radius:50%;background:var(--white);border:6px solid var(--ink)}
.brand-name{font-family:"Montserrat",sans-serif;font-weight:700;font-size:23px;color:var(--white);letter-spacing:.5px}
.nav{position:absolute;top:66px;font-family:"Montserrat",sans-serif;font-weight:600;font-size:16px;color:var(--white)}
.nav.active{color:var(--yellow)}
.search{position:absolute;left:944px;top:66px}
.login{position:absolute;left:982px;top:55px;width:105px;height:44px;border-radius:22px;background:var(--yellow);color:var(--white);font-family:"Montserrat",sans-serif;font-weight:600;font-size:16px;display:flex;align-items:center;justify-content:center;gap:6px}
.hero-title{position:absolute;left:110px;top:170px;font-family:"Montserrat",sans-serif;font-weight:700;font-size:74px;line-height:84px;color:var(--white)}
.hero-sub{position:absolute;left:113px;top:348px;width:470px;font-size:26px;line-height:40px;color:var(--white)}
.btn-ghost{position:absolute;top:456px;height:66px;border:2px solid var(--white);border-radius:33px;color:var(--white);font-family:"Montserrat",sans-serif;font-weight:600;font-size:17px;display:flex;align-items:center;justify-content:center}
.dots{position:absolute;left:569px;top:540px;display:flex;gap:5px}
.dots span{width:12px;height:12px;border-radius:50%;border:2px solid var(--white)}
.dots span.on{background:var(--white)}

/* welcome */
.welcome-box{position:absolute;left:113px;top:715px;width:593px;height:473px;border:2px solid var(--line)}
.h2{font-family:"Montserrat",sans-serif;font-weight:700;color:var(--ink)}
.welcome-title{position:absolute;left:158px;top:762px;font-size:40px;line-height:52px}
.welcome-text{position:absolute;left:158px;top:888px;width:450px;font-size:15px;line-height:26px;color:#444}
.btn-outline{position:absolute;left:158px;top:1081px;width:137px;height:48px;border:2px solid var(--yellow);border-radius:24px;color:var(--yellow);font-family:"Montserrat",sans-serif;font-weight:600;font-size:14px;display:flex;align-items:center;justify-content:center}
.video{position:absolute;left:636px;top:792px;width:452px;height:320px;background:linear-gradient(120deg,#8a8f96,#b9b3a7 45%,#6d7480);box-shadow:0 6px 18px rgba(0,0,0,.25)}
.play{position:absolute;left:826px;top:920px;width:64px;height:64px;border-radius:50%;background:var(--ink)}

/* services */
.services{position:absolute;left:0;top:1296px;width:1200px;height:1044px;background:var(--pale)}
.section-title{position:absolute;left:0;width:1200px;text-align:center;font-size:40px}
.spine{position:absolute;left:598px;top:1538px;width:3px;height:604px;background:var(--blue)}
.svc-icon{position:absolute;left:548px;width:104px;height:104px;border-radius:50%;border:5px solid var(--blue);background:var(--white);display:flex;align-items:center;justify-content:center}
.svc{position:absolute;width:370px}
.svc.left{left:122px;text-align:right}
.svc.right{left:701px;text-align:left}
.svc h3{font-family:"Montserrat",sans-serif;font-weight:600;font-size:22px;line-height:32px;color:var(--ink);margin-bottom:14px}
.svc p{font-size:14px;line-height:25px;color:var(--muted)}

/* testimonials */
.testimonials{position:absolute;left:0;top:2340px;width:1200px;height:403px;background:linear-gradient(100deg,#2d65b2,#1f5aa6 50%,#2a5fa8)}
.testimonials .section-title{color:var(--white);top:70px}
.quote{position:absolute;left:190px;top:150px;width:820px;text-align:center;font-style:italic;font-size:17px;line-height:31px;color:var(--white)}
.author{position:absolute;left:0;top:302px;width:1200px;text-align:center;font-family:"Montserrat",sans-serif;font-weight:700;font-size:20px;color:var(--white)}
.arrow{position:absolute;top:175px;width:54px;height:54px;border-radius:50%;border:2px solid var(--white);display:flex;align-items:center;justify-content:center}

/* booking */
.field{position:absolute;width:290px;height:48px;border:1.5px solid #9a9a9a;padding-left:18px;display:flex;align-items:center;font-size:15px;color:#333}
.submit{position:absolute;left:533px;top:3108px;width:134px;height:50px;border-radius:25px;background:var(--yellow);color:var(--white);font-family:"Montserrat",sans-serif;font-weight:700;font-size:16px;display:flex;align-items:center;justify-content:center}

/* footer */
.footer{position:absolute;left:0;top:3276px;width:1200px;height:324px;background:var(--footer);color:var(--white)}
.social{position:absolute;top:70px;width:52px;height:52px;border-radius:50%;border:2px solid var(--white)}
.f-line{position:absolute;left:0;width:1200px;text-align:center;font-size:14px;color:var(--white);display:flex;justify-content:center;align-items:center;gap:12px}
</style>
</head>
<body>

<header class="hero">
  <div class="hero-photo" role="img" aria-label="Yellow executive taxi driving along a blurred city street"></div>
  <div class="hero-shade"></div>
  <div class="brand"><span class="brand-mark"></span><span class="brand-name">MARLOW TRAVEL</span></div>
  <span class="nav active" style="left:461px">HOME</span>
  <span class="nav" style="left:541px">SERVICES</span>
  <span class="nav" style="left:647px">ABOUT US</span>
  <span class="nav" style="left:760px">VIP</span>
  <span class="nav" style="left:815px">CONTACT US</span>
  <svg class="search" width="18" height="18" viewBox="0 0 18 18"><circle cx="7.5" cy="7.5" r="5.5" fill="none" stroke="#fff" stroke-width="2.5"/><line x1="11.5" y1="11.5" x2="16" y2="16" stroke="#fff" stroke-width="2.5" stroke-linecap="round"/></svg>
  <div class="login"><svg width="12" height="14" viewBox="0 0 12 14"><rect x="1" y="6" width="10" height="8" rx="1" fill="#fff"/><path d="M3 6V4a3 3 0 0 1 6 0v2" fill="none" stroke="#fff" stroke-width="1.8"/></svg>LOGIN</div>
  <h1 class="hero-title">ALWAYS HERE<br>FOR YOU</h1>
  <p class="hero-sub">We are an executive Taxi firm with Chauffeur service</p>
  <a class="btn-ghost" style="left:113px;width:176px">BOOK ONLINE</a>
  <a class="btn-ghost" style="left:300px;width:176px">DRIVE WITH US</a>
  <div class="dots"><span class="on"></span><span></span><span></span><span></span></div>
</header>

<section class="welcome">
  <div class="welcome-box"></div>
  <h2 class="h2 welcome-title">WELCOME TO<br>MARLOW TRAVEL</h2>
  <p class="welcome-text">We provide airport transfers to and from all major UK airports, seaports, train station transfers and an executive business to business transfer service. Whether you have an individual or group transfer request, our company-owned fleet offers a choice of options to suit your needs, from luxury saloons and SUV's to 9-seat luxury transporters.</p>
  <a class="btn-outline">READ MORE</a>
  <div class="video" role="img" aria-label="Video still: hand holding a phone with a ride map on a city street"></div>
  <svg class="play" viewBox="0 0 64 64"><circle cx="32" cy="32" r="32" fill="#1b1b1b"/><path d="M26 20l18 12-18 12z" fill="#fff"/></svg>
</section>

<section class="services">
  <h2 class="h2 section-title" style="top:80px">SERVICES</h2>
</section>
<div class="spine"></div>

<div class="svc left" style="top:1488px"><h3>AIRPORT TRANSFERS</h3><p>Nam libero tempore, cum soluta nobis est eligendi optio cumque nihil impedit quo m solutainus id quod</p></div>
<div class="svc-icon" style="top:1486px"><svg width="44" height="44" viewBox="0 0 24 24"><path d="M21 16v-2l-8-5V3.5a1.5 1.5 0 0 0-3 0V9l-8 5v2l8-2.5V19l-2 1.5V22l3.5-1 3.5 1v-1.5L13 19v-5.5z" fill="#f2c414" transform="rotate(45 12 12)"/></svg></div>

<div class="svc right" style="top:1640px"><h3>TRAIN STATION TRANSFERS</h3><p>Nam libero tempore, cum soluta nobis est eligendi optio cumque nihil impedit quo m solutainus id quod</p></div>
<div class="svc-icon" style="top:1638px"><svg width="40" height="44" viewBox="0 0 20 22"><rect x="2" y="1" width="16" height="16" rx="3" fill="#f2c414"/><rect x="4.5" y="4" width="11" height="5" fill="#fff"/><circle cx="6" cy="13" r="1.5" fill="#fff"/><circle cx="14" cy="13" r="1.5" fill="#fff"/><path d="M5 17l-2 4M15 17l2 4" stroke="#f2c414" stroke-width="2"/></svg></div>

<div class="svc left" style="top:1789px"><h3>SEAPORT TRANSFERS</h3><p>Nam libero tempore, cum soluta nobis est eligendi optio cumque nihil impedit quo m solutainus id quod</p></div>
<div class="svc-icon" style="top:1789px"><svg width="44" height="44" viewBox="0 0 24 24"><rect x="9" y="3" width="6" height="4" fill="#f2c414"/><rect x="6" y="7" width="12" height="5" fill="#f2c414"/><path d="M3 12h18l-3 6H6z" fill="#f2c414"/><path d="M2 21c2 0 2-1 4-1s2 1 4 1 2-1 4-1 2 1 4 1 2-1 4-1" fill="none" stroke="#f2c414" stroke-width="1.6"/></svg></div>

<div class="svc right" style="top:1940px"><h3>HOLIDAY TRANSFERS</h3><p>Nam libero tempore, cum soluta nobis est eligendi optio cumque nihil impedit quo m solutainus id quod</p></div>
<div class="svc-icon" style="top:1940px"><svg width="46" height="40" viewBox="0 0 24 20"><path d="M4 8l2-5h12l2 5" fill="none" stroke="#f2c414" stroke-width="2"/><rect x="1" y="8" width="22" height="7" rx="2" fill="#f2c414"/><circle cx="5.5" cy="11.5" r="1.6" fill="#fff"/><circle cx="18.5" cy="11.5" r="1.6" fill="#fff"/><rect x="3" y="15" width="4" height="4" fill="#f2c414"/><rect x="17" y="15" width="4" height="4" fill="#f2c414"/></svg></div>

<div class="svc left" style="top:2074px"><h3>BUSINESS TO BUSINESS<br>PICK UP &amp; DROP OFF</h3><p>Nam libero tempore, cum soluta nobis est eligendi optio cumque nihil impedit quo m solutainus id quod</p></div>
<div class="svc-icon" style="top:2089px"><svg width="42" height="42" viewBox="0 0 24 24"><path d="M8 6V4h8v2" fill="none" stroke="#f2c414" stroke-width="2"/><rect x="2" y="6" width="20" height="15" rx="2" fill="#f2c414"/><path d="M7 6v15M17 6v15" stroke="#fff" stroke-width="1.2"/></svg></div>

<section class="testimonials" role="img" aria-label="Blue-tinted photo of a businessman riding in the back of a chauffeured car">
  <h2 class="h2 section-title">TESTIMONIALS</h2>
  <p class="quote">" At vero eos et accusamus et iusto odio dignissimos ducimus qui blanditiis praesentium voluptatum deleniti atque corrupti quos dolores et quas molestias excepturi sint occaecati cupiditate non provident, similique sunt in culpa qui officia deserunt mollitia animi, id est laborum et dolorum fuga. Et harum quidem rerum facilis est et expedita distinctio. Nam libero tempore, cum soluta nobis est eligendi optio cumque nihil impedit quo minus id quod "</p>
  <p class="author">- JOHN DOE</p>
  <div class="arrow" style="left:30px"><svg width="14" height="20" viewBox="0 0 14 20"><path d="M10 3L3 10l7 7" fill="none" stroke="#fff" stroke-width="2.5"/></svg></div>
  <div class="arrow" style="left:1120px"><svg width="14" height="20" viewBox="0 0 14 20"><path d="M4 3l7 7-7 7" fill="none" stroke="#fff" stroke-width="2.5"/></svg></div>
</section>

<section class="booking">
  <h2 class="h2 section-title" style="top:2846px">BOOK A RIDE WITH US</h2>
  <div class="field" style="left:151px;top:2942px">First Name:</div>
  <div class="field" style="left:455px;top:2942px">Last Name:</div>
  <div class="field" style="left:758px;top:2942px">Email:</div>
  <div class="field" style="left:151px;top:3007px">Phone:</div>
  <div class="field" style="left:455px;top:3007px">Date:</div>
  <div class="field" style="left:758px;top:3007px">Time:</div>
  <a class="submit">SUBMIT</a>
</section>

<footer class="footer">
  <span class="social" style="left:485px"></span>
  <span class="social" style="left:543px"></span>
  <span class="social" style="left:601px"></span>
  <span class="social" style="left:660px"></span>
  <p class="f-line" style="top:158px">
    <span><svg width="11" height="15" viewBox="0 0 12 16"><path d="M6 0a6 6 0 0 0-6 6c0 4.5 6 10 6 10s6-5.5 6-10a6 6 0 0 0-6-6zm0 8.5A2.5 2.5 0 1 1 6 3.5a2.5 2.5 0 0 1 0 5z" fill="#fff"/></svg> 14 Kestrel Row, Harbour Gate, Ashford TN24 8QP</span>
    <span>|</span>
    <span><svg width="14" height="14" viewBox="0 0 24 24"><path d="M6.6 10.8a15 15 0 0 0 6.6 6.6l2.2-2.2a1 1 0 0 1 1-.25 11.4 11.4 0 0 0 3.6.57 1 1 0 0 1 1 1V20a1 1 0 0 1-1 1A17 17 0 0 1 3 4a1 1 0 0 1 1-1h3.5a1 1 0 0 1 1 1c0 1.25.2 2.45.57 3.57a1 1 0 0 1-.25 1z" fill="#fff"/></svg> 07700 900418</span>
    <span>|</span>
    <span><svg width="16" height="12" viewBox="0 0 16 12"><rect width="16" height="12" rx="1" fill="#fff"/><path d="M1 1l7 6 7-6" fill="none" stroke="#121212" stroke-width="1.4"/></svg> info@marlowtravel.co.uk</span>
  </p>
  <p class="f-line" style="top:198px"><span>Help</span><span>|</span><span>FAQ</span><span>|</span><span>Support</span><span>|</span><span>Sitemap</span><span>|</span><span>Terms Of Use</span><span>|</span><span>Privacy Statement</span></p>
  <p class="f-line" style="top:236px">Copyrights © 2018, Marlow Travel. All rights reserved.</p>
</footer>

</body>
</html>
```